CBD AgriBusiness Verdant Trophy Business Card

We are HiTec producer of medical cannabis CBD Switzerland of high quality. Our website is alpinleaf.net, we will also revisit it graphically, the winner of this contest will be the graphic designer chosen for the new design of the website. We stand out by the skill of the team, many of our engineers we win cup cannabis. I join the current map to take as an example but to revisit completely: deletion of surname and first name, modification of funds (front / back), reorganization of text info, highlighting the address of the website. three characteristics define the business card: Professional, Class, refined. The business card must be optimized for soft-touch and selective varnish printing.

Target Market(s)

Customers and Suppliers

Industry/Entity Type

Agribusiness

Contact Information for Business Card

Logo, Tél / Whatsapp, mail, url du site : alpinleaf.net

Font styles to use
Sans Serif

Requirements
Must have
• Logo of alpinleaf.net
Nice to have
• a design that stands out well on the selective varnish
Should not have
• Last name and first name

```html
<!DOCTYPE html>
<html lang="en">
<head>
<meta charset="utf-8">
<title>alpinleaf business card</title>
<link href="https://fonts.googleapis.com/css2?family=Lato:wght@400;900&display=swap" rel="stylesheet">
<style>
  :root {
    --stage: #1a1a1a;
    --card: #0f0f10;
    --leaf-green: #8ccf5f;
    --silver: #b9b9b9;
    --text-light: #d8d8d8;
  }
  * { margin: 0; padding: 0; box-sizing: border-box; }
  html, body { width: 1200px; height: 900px; overflow: hidden; }
  body {
    background: var(--stage);
    font-family: "Lato", sans-serif;
    position: relative;
  }
  .card {
    position: absolute;
    width: 560px;
    height: 340px;
    background: var(--card);
    border-radius: 22px;
    display: flex;
    flex-direction: column;
    align-items: center;
    justify-content: center;
  }
  .card-front { left: 320px; top: 90px; }
  .card-back { left: 320px; top: 470px; }
  .brand {
    display: flex;
    align-items: center;
    gap: 14px;
    font-weight: 900;
    letter-spacing: 1px;
    line-height: 1;
  }
  .brand-mark { display: block; }
  .card-front .brand { font-size: 58px; color: var(--silver); }
  .card-front .brand-mark { width: 30px; height: 30px; background: var(--silver); }
  .card-back .brand { font-size: 62px; color: var(--leaf-green); margin-top: -20px; }
  .card-back .brand-mark { width: 32px; height: 32px; background: var(--leaf-green); }
  .contact-list {
    list-style: none;
    margin-top: 30px;
    margin-left: 60px;
  }
  .contact-item {
    display: flex;
    align-items: center;
    gap: 12px;
    color: var(--text-light);
    font-size: 19px;
    font-weight: 400;
    line-height: 30px;
  }
  .contact-icon { width: 18px; height: 18px; flex: none; }
</style>
</head>
<body>
  <section class="card card-front" aria-label="Card front">
    <div class="brand"><span class="brand-mark"></span><span class="brand-name">alpinleaf</span></div>
  </section>

  <section class="card card-back" aria-label="Card back">
    <div class="brand"><span class="brand-mark"></span><span class="brand-name">alpinleaf</span></div>
    <ul class="contact-list">
      <li class="contact-item">
        <svg class="contact-icon" viewBox="0 0 18 18" aria-hidden="true"><circle cx="9" cy="9" r="9" fill="var(--leaf-green)"/><path d="M6 4.5l2 2.2-1 1.2c.6 1.3 1.7 2.4 3 3l1.2-1 2.2 2-1 1.6c-3.6-.4-6.8-3.6-7.2-7.2z" fill="var(--card)"/></svg>
        <span>+41 79 555 01 23</span>
      </li>
      <li class="contact-item">
        <svg class="contact-icon" viewBox="0 0 18 18" aria-hidden="true"><rect x="1" y="3.5" width="16" height="11" rx="1" fill="var(--leaf-green)"/><path d="M1.5 4l7.5 6 7.5-6" fill="none" stroke="var(--card)" stroke-width="1.4"/></svg>
        <span>office@alpinleaf.net</span>
      </li>
      <li class="contact-item">
        <svg class="contact-icon" viewBox="0 0 18 18" aria-hidden="true"><circle cx="9" cy="9" r="9" fill="var(--leaf-green)"/><circle cx="9" cy="9" r="5.5" fill="none" stroke="var(--card)" stroke-width="1.3"/><path d="M3.5 9h11M9 3.5c-2.4 3-2.4 8 0 11M9 3.5c2.4 3 2.4 8 0 11" fill="none" stroke="var(--card)" stroke-width="1.1"/></svg>
        <span>www.alpinleaf.net</span>
      </li>
    </ul>
  </section>
</body>
</html>
```